Bifold brochure design for leadership academy

Please see below. This is a bifold brochure for a leadership academy. (www.brv.institute). Look and feel must be colours, shapes, abstract designs, graphics, pictures. Make this professional, yet casual and bold.

Feel free to design just the front and back cover, then I'll give feedback on whether or not you're in the right direction.

COVER
- Title: “The Boldest Bridge Year Journey”
- “Northward Mentor Institute” logo somewhere
- Subtitles (with images, icons, and/or shapes): “Self-discovery” “Skills development” “Real-world Impact”

PAGE 2 (Inside Fold)
- Title: "The Program"
- Section 2a: Section title: "How it works”
- Image: See website, image under "four phases of the program". Please adapt and make it look better
- Text: NMI is a structured, 8-month ‘gap year’ program for 18-25 year olds who want more than just a year off – they want a year ahead. Our aim is to develop high-potential young leaders with strong values, clear purpose, high-impact skills, and a track record of real-world accomplishments that are second-to-none. We do this through four-phases.
- Section 2b: Section title: “Dates & Timing”
- Image: See image on website under 'dates and timing'. Make sure both dates show up on the brochure (September and January program).
- Text: There are two programs per year: one that starts in September, the other in January. The first four months of the program are based in Toronto at the NMI headquarters. The curriculum we work through is highly engaging and personalized, focusing directly on students’ goals. After that, students are out in the world, achieving the remaining components of the program (e.g. internship, volunteer abroad).

PAGE 3 (Outside Fold)
- Page Title: "The Students"
- Section 3a: Section title: “Who’s it for”
- Subtitle1: “High school graduates”
 Image/icon of a high school grad
 Text1: 90% of high school grads aren't sure why they’re going to university or what they want to study.
 Text2: NMI helps students discover what they truly want to do in life, and make enormous progress towards these goals.

- Subtitle2: “Post-secondary students”
 Image/icon of a university / college student
 Text1: 28% of students switch or drop out of their program because it wasn’t for them or they didn’t like it.
 Text2: Don't keep moving around or risk switching careers down the road – find out what sparks your passion with NMI.

- Subtitle3: “Post-secondary graduates”
 Image/icon of a university/ college grad
 Text1: 50% of graduates are unemployed or underemployed, 60% are in debt.
 Text2: NMI will help you get your dream job – our students won’t settle for anything less.

- Section 3b: Section title: “How to apply”
 Text1: We select high-potential young leaders with a desire to improve themselves and impact the world.
 Text2: We won’t ask you for your grades – we care more about your values and potential.
 Text3: Visit www.brv.institute to apply now

BACK COVER
- Page Title: “Get in Touch”
- Website: www.brv.institute
- Facebook page: facebook.com/brv.institute
- Twitter handle: @brv_institute
- Email: tomas@brv.institute

Project Deadline Extended Reason: Made a mistake initially only giving designers 2 days to submit. This allows for more high quality designs. Thank you. Added Wednesday, March 18, 2015

Target Market(s)

18-25 year olds, parents, teachers

Industry/Entity Type

Leadership

Requirements
Must have
• Beautiful design - sleek and bold, yet colourful and casual. Keep the colours similar to our website (www.brv.institute). See examples of other brochures.
• http://img.pelvoro.net/jpg/00/11/22/33/240_F_11223344_xQr8LmPzTw3KdNvBsYcHuJeFa2gkTqWn.jpg
• http://vantoliq.com/wp-content/uploads/2014/11/Real-Estate-Bi-fold-Brochure.jpg
• http://www.murablo.com/media/k2/galleries/5/001-bi-fold-brochure-psd-mock-up-template.jpg
• http://img.pelvoro.net/jpg/00/44/55/66/240_F_44556677_Zk3wPqLm8RtYvBnXcDs2HjKuE5fa9Gq0.jpg

```html
<!DOCTYPE html>
<html lang="en">
<head>
<meta charset="utf-8">
<title>NMI Bifold Brochure – Inside Spread</title>
<link rel="stylesheet" href="https://fonts.googleapis.com/css2?family=Montserrat:wght@400;600;700;800&family=Nunito+Sans:wght@400;600;700&display=swap">
<style>
:root{
  --bg:#e8e8e8;
  --paper:#f3f7fa;
  --stripe:#d8ebf4;
  --stripe-soft:#e6f2f8;
  --navy:#1a5a98;
  --navy-dark:#134a82;
  --red:#c8202a;
  --ink:#1c1c1c;
  --muted:#3a3a3a;
  --phase-1:#dce9e9;
  --phase-2:#f6e6c8;
  --phase-3:#c9c3e6;
  --phase-4:#bfe2c6;
  --col-a:#fbf6d3;
  --col-b:#f7efc4;
  --col-c:#f4e2c5;
  --apply:#f4e3c8;
}
*{box-sizing:border-box;margin:0;padding:0}
html,body{width:1200px;height:909px;overflow:hidden;background:var(--bg)}
body{position:relative;font-family:"Nunito Sans",Arial,sans-serif;color:var(--ink)}
.spread{position:absolute;left:190px;top:95px;width:820px;height:700px;display:flex}
.page{position:relative;width:410px;height:700px;overflow:hidden;
  background:
    repeating-linear-gradient(180deg,transparent 0 14px,var(--stripe-soft) 14px 22px,transparent 22px 40px),
    linear-gradient(180deg,var(--paper),#fbfdfe 60%,var(--paper));}
.page--left{border-right:1px solid #d3dde3}
.sky{position:absolute;left:0;right:0;top:0;height:48px;
  background:repeating-linear-gradient(180deg,var(--stripe) 0 8px,#edf6fa 8px 16px)}
.band{position:absolute;left:0;right:0;top:48px;height:76px;background:var(--navy);
  box-shadow:inset 0 -6px 0 var(--navy-dark)}
.page--right .band{top:50px;height:88px}
.page-title{position:absolute;left:55px;top:56px;font-family:Montserrat,Arial,sans-serif;
  font-weight:800;font-size:34px;line-height:31px;color:#fff;letter-spacing:-0.5px}
.page--right .page-title{left:50px;top:66px}
.badge{position:absolute;width:84px;height:84px;border-radius:50%;background:var(--red)}
.badge .glyph{position:absolute;left:22px;top:24px;width:40px;height:36px;border-radius:4px;background:#7d0f15}
.shard{position:absolute}
.section-title{position:absolute;font-family:Montserrat,Arial,sans-serif;font-weight:700;font-size:15px;color:var(--ink);letter-spacing:0.2px}
.body-copy{position:absolute;font-size:11px;line-height:13px;letter-spacing:-0.2px;color:var(--muted)}
/* phases */
.phases{position:absolute;left:40px;top:262px;width:362px;height:146px;display:flex}
.phase{position:relative;flex:1;padding:4px 5px 0 5px}
.phase--discover{background:var(--phase-1)}
.phase--design{background:var(--phase-2)}
.phase--build{background:var(--phase-3)}
.phase--achieve{background:var(--phase-4)}
.phase-num{position:absolute;left:-4px;top:-6px;width:14px;height:14px;border-radius:50%;background:var(--red);
  color:#fff;font:700 9px/14px Montserrat,Arial,sans-serif;text-align:center}
.phase-name{font-family:Montserrat,Arial,sans-serif;font-weight:700;font-size:11.5px;padding-left:14px;margin-top:-1px}
.phase-art{width:40px;height:36px;margin:6px auto 6px;border-radius:6px;background:rgba(30,30,30,.55)}
.phase-text{font-size:6.4px;line-height:8px;color:#444}
.phase-text ol{padding-left:9px}
/* timeline */
.timeline{position:absolute;left:40px;top:532px;width:354px;height:122px;display:grid;grid-template-columns:repeat(12,1fr)}
.month{font-family:Montserrat,Arial,sans-serif;font-weight:700;font-size:8.6px;text-align:center;padding-top:2px;height:122px}
.month:nth-child(odd){background:var(--col-a)}
.month:nth-child(even){background:var(--col-b)}
.month:nth-child(n+11){background:var(--col-c)}
.event{position:absolute;font-size:5.2px;line-height:6px;color:#333;white-space:nowrap}
.event::before{content:"";position:absolute;left:-7px;top:0;width:5px;height:5px;border-radius:50%;background:var(--red)}
.event b{font-weight:700}
.mark{position:absolute;left:46px;top:560px;font-family:Montserrat,Arial,sans-serif;font-weight:800;font-size:10px;color:var(--red)}
/* students */
.photo{position:absolute;left:10px;top:210px;width:146px;height:275px;
  background:linear-gradient(160deg,#e9e4de 0%,#c9b8a8 35%,#2c2c2c 70%,#141414 100%)}
.audience{position:absolute;left:166px;top:200px;width:232px}
.audience h3{font-family:Montserrat,Arial,sans-serif;font-weight:700;font-size:12.2px;margin:8px 0 3px}
.audience ul,.apply ul{list-style:none}
.audience li,.apply li{position:relative;padding-left:11px;font-size:10.6px;line-height:12.6px;color:var(--muted);margin-bottom:3px}
.audience li::before,.apply li::before{content:"";position:absolute;left:1px;top:5px;width:3px;height:3px;border-radius:50%;background:#333}
.apply{position:absolute;left:10px;top:520px;width:385px;height:142px;background:var(--apply)}
.apply .section-title{left:52px;top:15px}
.apply-icon{position:absolute;left:64px;top:48px;width:42px;height:48px;background:#cfe2df;border-radius:2px}
.apply ul{position:absolute;left:118px;top:48px;width:250px}
</style>
</head>
<body>
<main class="spread">
  <section class="page page--left">
    <div class="sky"></div>
    <div class="band"></div>
    <h1 class="page-title">The<br>Program</h1>
    <div class="badge" style="left:210px;top:28px" role="img" aria-label="Open book icon"><span class="glyph"></span></div>
    <svg class="shard" style="left:330px;top:130px" width="60" height="24"><polygon points="0,4 60,0 48,24" fill="#9fd0e6" opacity=".6"/></svg>

    <h2 class="section-title" style="left:40px;top:158px">HOW IT WORKS</h2>
    <p class="body-copy" style="left:40px;top:177px;width:368px">NMI is a structured, 8-month ‘gap year’ program for 18-25 year olds who want more than just a year off – they want a year ahead. Our aim is to develop high-potential young leaders with strong values, clear purpose, high-impact skills, and a track record of real-world accomplishments that are second-to-none. We do this through four-phases.</p>

    <div class="phases">
      <div class="phase phase--discover"><span class="phase-num">1</span><div class="phase-name">Discover</div>
        <div class="phase-art" role="img" aria-label="Compass icon for purpose, direction and passion"></div>
        <p class="phase-text">Discover your strengths, development areas, personality style, passions and other attributes through a highly personalized transformation program.</p></div>
      <div class="phase phase--design"><span class="phase-num">2</span><div class="phase-name">Discover</div>
        <div class="phase-art" role="img" aria-label="Goal sheet icon"></div>
        <p class="phase-text">Design your year in the program and learn how to manage goals through our advanced goal-setting training.</p></div>
      <div class="phase phase--build"><span class="phase-num">3</span><div class="phase-name">Build</div>
        <div class="phase-art" role="img" aria-label="Speaker at podium icon"></div>
        <p class="phase-text">Build a set of skills that will directly help you achieve your goals, including issue-based problem solving, creativity, and structured communications.</p></div>
      <div class="phase phase--achieve"><span class="phase-num">4</span><div class="phase-name">Achieve</div>
        <div class="phase-art" role="img" aria-label="Group achievement icons"></div>
        <div class="phase-text">Achieve six things before you can graduate:
          <ol><li>Solve a social problem</li><li>Conquer a physical feat</li><li>Organize an event</li><li>Volunteer abroad</li><li>Start something</li><li>Do an internship</li></ol></div></div>
    </div>

    <h2 class="section-title" style="left:40px;top:424px">DATES &amp; TIMING</h2>
    <p class="body-copy" style="left:40px;top:443px;width:368px">There are two programs per year: one that starts in September, the other in January. The first four months of the program are based in Toronto at the NMI headquarters. The curriculum we work through is highly engaging and personalized, focusing directly on students’ goals. After that, students are out in the world, achieving the remaining components of the program (e.g. internship, volunteer abroad).</p>

    <div class="timeline">
      <div class="month">AUG</div><div class="month">SEP</div><div class="month">OCT</div><div class="month">NOV</div>
      <div class="month">DEC</div><div class="month">JAN</div><div class="month">FEB</div><div class="month">MAR</div>
      <div class="month">APR</div><div class="month">MAY</div><div class="month">JUN</div><div class="month">JUL</div>
    </div>
    <span class="mark">NMI</span>
    <span class="event" style="left:80px;top:552px"><b>Discover:</b> find your purpose,<br>passion &amp; direction.</span>
    <span class="event" style="left:80px;top:570px"><b>Design:</b> design your goal</span>
    <span class="event" style="left:80px;top:584px"><b>Build:</b> build relevant skills<br>for life and career</span>
    <span class="event" style="left:80px;top:602px"><b>Achieve:</b> solve your<br>social problems</span>
    <span class="event" style="left:80px;top:619px"><b>Conquer</b> a physical feat</span>
    <span class="event" style="left:80px;top:633px"><b>Organize</b> an event</span>
    <span class="event" style="left:209px;top:562px"><b>Monthly</b> checkpoint</span>
    <span class="event" style="left:235px;top:577px"><b>Monthly</b> checkpoint</span>
    <span class="event" style="left:264px;top:590px"><b>Monthly</b> checkpoint</span>
    <span class="event" style="left:294px;top:603px"><b>Monthly</b> checkpoint</span>
    <span class="event" style="left:209px;top:616px"><b>Volunteer</b> abroad</span>
    <span class="event" style="left:294px;top:630px"><b>Do</b> an internship</span>
    <span class="event" style="left:209px;top:633px"><b>Start</b> something</span>
  </section>

  <section class="page page--right">
    <div class="sky"></div>
    <div class="band"></div>
    <h1 class="page-title">The<br>Students</h1>
    <div class="badge" style="left:210px;top:28px" role="img" aria-label="Two students icon"><span class="glyph"></span></div>
    <svg class="shard" style="left:340px;top:142px" width="60" height="70"><polygon points="0,0 60,15 40,70" fill="#a8d5ea" opacity=".55"/></svg>
    <svg class="shard" style="left:350px;top:360px" width="60" height="150"><polygon points="60,0 60,150 0,110" fill="#a8d5ea" opacity=".5"/></svg>

    <h2 class="section-title" style="left:62px;top:170px">WHO’S IT FOR</h2>
    <div class="photo" role="img" aria-label="Photo of two graduates in caps and gowns holding a diploma"></div>
    <div class="audience">
      <h3>High school graduates</h3>
      <ul><li>90% of high school grads aren’t sure why they’re going to university or what they want to study.</li>
        <li>NMI helps students discover what they truly want to do in life, and make enormous progress towards these goals.</li></ul>
      <h3>Post-secondary students</h3>
      <ul><li>28% of students switch or drop out of their program because it wasn’t for them or they didn’t like it.</li>
        <li>Don’t keep moving around or risk switching careers down the road – find out what sparks your passion with NMI.</li></ul>
      <h3>Post-secondary graduates</h3>
      <ul><li>50% of graduates are unemployed or underemployed, 60% are in debt.</li>
        <li>NMI will help you get your dream job – our students won’t settle for anything less.</li></ul>
    </div>

    <div class="apply">
      <h2 class="section-title">HOW TO APPLY</h2>
      <div class="apply-icon" role="img" aria-label="Tablet application icon"></div>
      <ul><li>We select high-potential young leaders with a desire to improve themselves and impact the world.</li>
        <li>We won’t ask you for your grades – we care more about your values and potential.</li>
        <li>Visit www.brv.institute to apply now</li></ul>
    </div>
  </section>
</main>
</body>
</html>
```